Valdane Companies Business Card Design

We need a new business card for our Private Equity Real Estate Development firm, “Valdane” and our EB-5 regional center “Thornmere Regional Center” on one card. We prefer a design that is simple, elegant, and represents the luxury products we design and build as well as the financial security and stability our successful history has produced. We are an industry leader in our field and 3rd generation family business that has evolved into an institutional quality investment platform. Considered design size is standard business card dimensions (3.5 x 2 inches with an additional 1/8 inch space for design elements or backgrounds that extend beyond the finished size of your piece.

Target Market(s)

• High net worth individuals
• Highly skilled technical workers and physicians in the US seeking investment-based immigration opportunities
• Sophisticated private equity investors
• Intermediary partners include domestic attorneys and investment brokers, as well as international agent networks
• US real estate developers

Industry/Entity Type

Finance

Contact Information for Business Card

(Providing placeholder info for personal information, please design for longer character spaces, longer names and addresses etc..)
• Logo for Valdane
• Logo for Thornmere Regional Center
• Full name: Marcus Valdane
• Job title: CEO
• Email address: mvaldane@valdanecompanies.com
• Cell phone number: +1.555.314.2287
• Office number +1.555.628.4410
• Office address: Larkfield Court 5, 4817 Vista Orilla, Cresthaven, WL.
• Website: www.valdanecompanies.com

Font styles to use
Serif
Sans Serif

Colors
ec1f27
ffffff
000000

Requirements
Must have
• • Logo for Valdane
• • Logo for Thornmere Regional Center
• - Use rounded corners
• (See .ai file included for logos)
Nice to have
• • Simple, elegant design
• • Aesthetically compatible with our website design (www.valdanecompanies.com)
• • Color palette including but not limited to white, black, and red (as per logos)
Should not have
• - Not too much red color
• - Do not stack both logos on top of each other

```html
<!DOCTYPE html>
<html lang="en">
<head>
<meta charset="utf-8">
<title>Valdane Companies – Business Card</title>
<link rel="stylesheet" href="https://fonts.googleapis.com/css2?family=Noto+Serif:wght@400;700&family=Roboto:wght@400;500&display=swap">
<style>
  :root {
    --red: #d71f3c;
    --white: #ffffff;
    --black: #0d0d0d;
    --ink: #3a3a3a;
    --ink-soft: #555555;
    --stage: #2b2e33;
    --serif: "Noto Serif", Georgia, serif;
    --sans: "Roboto", Arial, sans-serif;
  }
  * { box-sizing: border-box; margin: 0; padding: 0; }
  html, body { width: 1200px; height: 900px; overflow: hidden; }
  body {
    background: var(--stage);
    display: flex;
    flex-direction: column;
    align-items: center;
    justify-content: center;
    gap: 50px;
  }
  .card {
    position: relative;
    width: 630px;
    height: 360px;
    border-radius: 14px;
    overflow: hidden;
  }

  /* Front: contact side */
  .card-front { background: var(--white); }
  .name-ribbon {
    position: absolute;
    top: 34px; left: 0;
    width: 360px; height: 46px;
    background: var(--red);
    clip-path: polygon(0 0, 100% 0, 93% 100%, 0 100%);
    display: flex; align-items: center;
    padding-left: 48px;
  }
  .name-ribbon .person-name {
    font-family: var(--serif);
    font-size: 25px;
    color: var(--white);
    white-space: nowrap;
  }
  .job-title {
    position: absolute;
    top: 88px; left: 48px;
    font-family: var(--sans);
    font-size: 16px;
    color: var(--ink);
  }
  .contact-list {
    position: absolute;
    top: 136px; left: 48px;
    list-style: none;
    font-family: var(--sans);
    font-size: 15px;
    color: var(--ink);
  }
  .contact-list li {
    display: flex; align-items: center; gap: 12px;
    height: 25px;
    white-space: nowrap;
  }
  .contact-list svg { width: 15px; height: 15px; flex: none; }
  .brand-mark {
    position: absolute;
    top: 150px; right: 48px;
    display: flex; align-items: center; gap: 12px;
  }
  .brand-mark .mark-square {
    width: 24px; height: 24px;
    background: var(--ink);
  }
  .brand-mark .brand-name {
    font-family: var(--serif);
    font-weight: 700;
    font-size: 26px;
    color: var(--ink);
    white-space: nowrap;
  }
  .office-address {
    position: absolute;
    right: 48px; bottom: 56px;
    text-align: right;
    font-family: var(--sans);
    font-style: normal;
    font-size: 15px;
    line-height: 1.45;
    color: var(--ink-soft);
    white-space: nowrap;
  }
  .footer-band {
    position: absolute;
    left: 0; right: 0; bottom: 0;
    height: 36px;
    background: var(--red);
    clip-path: polygon(0 100%, 36% 0, 100% 0, 100% 100%);
  }

  /* Back: regional center side */
  .card-back {
    background: var(--black);
    display: flex; align-items: center; justify-content: center;
  }
  .center-mark {
    display: flex; align-items: center; gap: 16px;
  }
  .center-mark .mark-circle {
    width: 30px; height: 30px;
    border-radius: 50%;
    background: var(--red);
  }
  .center-mark .center-name {
    font-family: var(--serif);
    font-weight: 700;
    font-size: 34px;
    color: var(--red);
    white-space: nowrap;
  }
</style>
</head>
<body>

  <section class="card card-front" aria-label="Business card, contact side">
    <div class="name-ribbon"><span class="person-name">Marcus Valdane</span></div>
    <p class="job-title">CEO</p>

    <ul class="contact-list">
      <li>
        <svg viewBox="0 0 16 16" aria-hidden="true"><rect x="4" y="1" width="8" height="14" rx="1.5" fill="none" stroke="var(--red)" stroke-width="1.6"/><circle cx="8" cy="12.5" r="0.9" fill="var(--red)"/></svg>
        +1.555.314.2287
      </li>
      <li>
        <svg viewBox="0 0 16 16" aria-hidden="true"><path d="M1.5 6c0-2 3-3.5 6.5-3.5S14.5 4 14.5 6l-3 .8-.5-1.8h-6l-.5 1.8zM3.5 8h9l1 6h-11z" fill="var(--red)"/><circle cx="8" cy="11" r="1.6" fill="var(--white)"/></svg>
        +1.555.628.4410
      </li>
      <li>
        <svg viewBox="0 0 16 16" aria-hidden="true"><rect x="1" y="3" width="14" height="10" fill="var(--red)"/><path d="M1 3l7 6 7-6" fill="none" stroke="var(--white)" stroke-width="1.3"/></svg>
        mvaldane@valdanecompanies.com
      </li>
      <li>
        <svg viewBox="0 0 16 16" aria-hidden="true"><circle cx="8" cy="8" r="7" fill="var(--red)"/><g fill="none" stroke="var(--white)" stroke-width="1"><ellipse cx="8" cy="8" rx="3" ry="7"/><path d="M1 8h14M2 4.5h12M2 11.5h12"/></g></svg>
        www.valdanecompanies.com
      </li>
    </ul>

    <div class="brand-mark">
      <span class="mark-square"></span>
      <span class="brand-name">Valdane Capital</span>
    </div>

    <address class="office-address">
      Larkfield Court 5, 4817<br>
      Vista Orilla, Cresthaven, WL
    </address>

    <div class="footer-band"></div>
  </section>

  <section class="card card-back" aria-label="Business card, regional center side">
    <div class="center-mark">
      <span class="mark-circle"></span>
      <span class="center-name">Thornmere Regional Center</span>
    </div>
  </section>

</body>
</html>
```